Wine label for premium wine of vinery Mirelovac.

Design Premium wine label.

The brand is called Telvora. Brand can be extended to Ambero Telvora. There
The label should be unique and high class feeling.
This is facebook lonk of the winery
https://www.sociloop.net/402918375510264/

On facebook you can see some examole of labels that are used now. Winery is called Mirelovac, so they used letter "M" as a logo in different ways
Updates

Need extra days to review

Target Market(s)

Premium high class yet modern living traditional but also gadget fun.
I have uploaded few inspirational photos that the owner of the vinery likes. Hope it helps.

Industry/Entity Type

Vinery

Requirements
Must have
• Black, gold, silver color to be dominated. Colors that are NOT acceptable are: green, yellow, blue, purple, pink.

The name of the vinary is Mirelovac and it should be on the front label.
Nice to have
• The size of label should fit the Sorbelo application screenshot frame.
Should not have
• Cheap perception of the label and brand

```html
<!DOCTYPE html>
<html lang="en">
<head>
<meta charset="utf-8">
<title>Telvora – Mirelovac Wine Label</title>
<link rel="stylesheet" href="https://fonts.googleapis.com/css2?family=Crimson+Text:wght@400;600&family=Allura&display=swap">
<style>
  :root {
    --page: #ffffff;
    --label-dark: #333333;
    --label-mid: #3d3d3d;
    --label-light: #474747;
    --gold: #c9a45c;
    --gold-deep: #a9823f;
    --ink-white: #f2f0ec;
    --engraving: #2a2a2a;
    --engraving-soft: #4a4a4a;
    --accent-red: #8e1f22;
  }
  * { margin: 0; padding: 0; box-sizing: border-box; }
  html, body {
    width: 1200px;
    height: 1200px;
    overflow: hidden;
    background: var(--page);
  }
  .canvas {
    position: relative;
    width: 1200px;
    height: 1200px;
    background: var(--page);
  }
  .wine-label {
    position: absolute;
    left: 220px;
    top: 170px;
    width: 760px;
    height: 860px;
    background: linear-gradient(180deg, var(--label-light) 0%, var(--label-mid) 45%, var(--label-dark) 100%);
    color: var(--ink-white);
    font-family: "Crimson Text", Georgia, serif;
    text-align: center;
    overflow: hidden;
  }
  .winery-name {
    position: absolute;
    top: 34px;
    left: 0;
    right: 0;
    font-size: 33px;
    font-weight: 600;
    letter-spacing: 4px;
    text-transform: uppercase;
  }
  .accent-drop {
    position: absolute;
    top: 82px;
    left: 474px;
    width: 22px;
    height: 16px;
    border-radius: 50%;
    background: var(--accent-red);
    transform: rotate(25deg);
  }
  .winery-mark {
    position: absolute;
    top: 140px;
    left: 0;
    right: 0;
    display: flex;
    align-items: center;
    justify-content: center;
    gap: 16px;
  }
  .winery-mark__dot {
    width: 22px;
    height: 22px;
    border-radius: 50%;
    border: 2px solid var(--gold);
  }
  .winery-mark__name {
    font-family: "Crimson Text", Georgia, serif;
    font-weight: 400;
    font-size: 44px;
    color: var(--gold);
  }
  .vineyard-scene {
    position: absolute;
    top: 250px;
    left: 0;
    width: 760px;
    height: 330px;
  }
  .wine-name {
    position: absolute;
    top: 555px;
    left: 0;
    right: 0;
    font-family: "Allura", cursive;
    font-size: 150px;
    line-height: 1;
    color: var(--gold);
  }
  .grape-variety {
    position: absolute;
    top: 738px;
    left: 0;
    right: 0;
    font-size: 36px;
  }
  .origin {
    position: absolute;
    top: 794px;
    left: 0;
    right: 0;
    font-size: 36px;
  }
</style>
</head>
<body>
  <main class="canvas">
    <section class="wine-label">
      <h1 class="winery-name">Mirelovac</h1>
      <span class="accent-drop" aria-hidden="true"></span>

      <div class="winery-mark">
        <span class="winery-mark__dot" aria-hidden="true"></span>
        <span class="winery-mark__name">Mirelovac</span>
      </div>

      <svg class="vineyard-scene" viewBox="0 0 760 330" role="img" aria-label="Engraved illustration of rolling vineyard hills with a farmhouse and cypress trees">
        <defs>
          <radialGradient id="scene-tone" cx="50%" cy="45%" r="60%">
            <stop offset="0%" stop-color="#2f2f2f"/>
            <stop offset="70%" stop-color="#383838"/>
            <stop offset="100%" stop-color="#3e3e3e" stop-opacity="0"/>
          </radialGradient>
        </defs>
        <ellipse cx="380" cy="170" rx="380" ry="150" fill="url(#scene-tone)"/>
        <path d="M0 300 L60 296 L120 302 L200 294 L280 300 L360 292 L440 299 L520 293 L600 300 L680 291 L760 297 L760 330 L0 330 Z" fill="var(--label-mid)"/>
        <path d="M0 300 L60 296 L120 302 L200 294 L280 300 L360 292 L440 299 L520 293 L600 300 L680 291 L760 297" fill="none" stroke="#555555" stroke-width="2"/>
      </svg>

      <p class="wine-name">Telvora</p>
      <p class="grape-variety">Sauvignon Blanc</p>
      <p class="origin">Croatia</p>
    </section>
  </main>
</body>
</html>
```